New Innovative Counselling and psychotherapy Service needs Business Card design

Keep it simple and professional. On one side, just company name and logo (perhaps in all blue) and maybe a tag line.

On other side (all white) my name and Qualifications in centre

Industry/Entity Type

Health And Wellness

Contact Information for Business Card

Dara Whelby
Counsellor & Psychotherapist
BSc (Psychol.), BA, Dip. (Couns. & Psych.), PG.Cert (CBT), FGTrK, ONRE

I will also require Mobile no, Email and web site address of which I'll pass on to final designer.

Font styles to use
Sans Serif

Requirements
Must have
• My Logo Only and please use the colours in logo that is in it.
Should not have
• Any other images

```html
<!DOCTYPE html>
<html lang="en">
<head>
<meta charset="utf-8">
<title>Calmera Grove – Business Card</title>
<link rel="stylesheet" href="https://fonts.googleapis.com/css2?family=Roboto:wght@300;400;700&display=swap">
<style>
  :root {
    --page: #e9e9ea;
    --sky: #4fb6ea;
    --sky-deep: #3d9fd6;
    --leaf: #7ab648;
    --ink: #333638;
    --ink-soft: #4a4d50;
    --paper: #f6f6f6;
    --ghost: #e6e6e7;
    --white: #ffffff;
  }
  * { box-sizing: border-box; margin: 0; padding: 0; }
  html, body {
    width: 1200px; height: 726px; overflow: hidden;
    background: var(--page);
    font-family: "Roboto", Arial, sans-serif;
  }
  .sheet {
    position: relative; width: 1200px; height: 726px;
    display: flex; align-items: center; justify-content: center; gap: 40px;
  }
  .card {
    position: relative; width: 540px; height: 309px; overflow: hidden;
    box-shadow: 0 6px 18px rgba(0,0,0,0.12);
  }

  /* Front */
  .card-front { background: var(--sky); }
  .front-brand {
    position: absolute; left: 0; right: 0; top: 110px;
    display: flex; align-items: center; justify-content: center; gap: 14px;
  }
  .brand-dot { width: 54px; height: 54px; border-radius: 50%; background: var(--white); flex: none; }
  .front-text { color: var(--white); }
  .front-name { font-size: 34px; font-weight: 300; letter-spacing: 0.5px; line-height: 1; }
  .front-tagline { margin-top: 8px; font-size: 13px; font-weight: 400; letter-spacing: 6px; }

  /* Back */
  .card-back { background: var(--paper); }
  .back-band {
    position: absolute; left: 0; top: 0; bottom: 0; width: 68px;
    background: var(--sky-deep); border-right: 4px solid var(--leaf);
  }
  .back-ghost {
    position: absolute; right: -60px; top: -40px; width: 300px; height: 300px;
    border-radius: 50%; background: var(--ghost);
  }
  .back-brand {
    position: absolute; left: 92px; top: 36px;
    display: flex; align-items: center; gap: 14px;
  }
  .back-brand .brand-dot { width: 48px; height: 48px; background: var(--sky); }
  .back-name { font-size: 30px; font-weight: 300; color: var(--ink); letter-spacing: 0.3px; }
  .holder { position: absolute; left: 92px; top: 118px; }
  .holder-name { font-size: 20px; font-weight: 700; color: var(--sky-deep); margin-bottom: 4px; }
  .holder-role, .holder-quals { font-size: 11.5px; color: var(--ink-soft); line-height: 1.35; }
  .contact { position: absolute; left: 92px; top: 208px; list-style: none; }
  .contact li {
    display: flex; align-items: center; gap: 10px;
    font-size: 13px; color: var(--ink-soft); line-height: 1; margin-bottom: 9px;
  }
  .contact svg { width: 13px; height: 13px; flex: none; }
</style>
</head>
<body>
<main class="sheet">
  <section class="card card-front" aria-label="Card front">
    <div class="front-brand">
      <span class="brand-dot"></span>
      <div class="front-text">
        <div class="front-name">Calmera Grove</div>
        <div class="front-tagline">A tag line goes here</div>
      </div>
    </div>
  </section>

  <section class="card card-back" aria-label="Card back">
    <div class="back-ghost"></div>
    <div class="back-band"></div>
    <div class="back-brand">
      <span class="brand-dot"></span>
      <span class="back-name">Calmera Grove</span>
    </div>
    <div class="holder">
      <div class="holder-name">Dara Whelby</div>
      <div class="holder-role">Counsellor &amp; Psychotherapist</div>
      <div class="holder-quals">BSc (Psychol.), BA, Dip. (Couns. &amp; Psych.),<br>PG.Cert (CBT), FGTrK, ONRE</div>
    </div>
    <ul class="contact">
      <li>
        <svg viewBox="0 0 16 16" aria-hidden="true"><path fill="#3d9fd6" d="M3 1.5l2.5 0 1.2 3-1.6 1.2a8 8 0 0 0 5.2 5.2l1.2-1.6 3 1.2v2.5c0 .8-.7 1.5-1.5 1.5A12.5 12.5 0 0 1 1.5 3c0-.8.7-1.5 1.5-1.5z"/></svg>
        1234 555 0190
      </li>
      <li>
        <svg viewBox="0 0 16 16" aria-hidden="true"><rect x="1" y="3" width="14" height="10" rx="1" fill="#3d9fd6"/><path d="M1.5 3.5L8 9l6.5-5.5" stroke="#fff" stroke-width="1.3" fill="none"/></svg>
        dara.w@CalmeraGrove.com
      </li>
      <li>
        <svg viewBox="0 0 16 16" aria-hidden="true"><circle cx="8" cy="8" r="6.5" fill="#7ab648"/><path d="M1.5 8h13M8 1.5c-3 3.5-3 9.5 0 13M8 1.5c3 3.5 3 9.5 0 13" stroke="#fff" stroke-width="1" fill="none"/></svg>
        www.CalmeraGrove.com
      </li>
    </ul>
  </section>
</main>
</body>
</html>
```